Musical download and streaming website

hello designers, I want to start up a musical website where users can download and rate music of different genres such as RnB, Hip hop, rock, afro-pop. This website should be attractive and contemporary. There will be a search column for different songs. Music files will be mp3, mwa, and others. I like blue, gold, pink and indigo colors. My website should resemble http://tunovalt.com. There should be good imaginary of music stars on my website.

```html
<!DOCTYPE html>
<html lang="en">
<head>
<meta charset="utf-8">
<title>Velora Music</title>
<link href="https://fonts.googleapis.com/css2?family=Lato:ital,wght@0,400;0,700;0,900;1,400&family=Open+Sans:wght@700;800&display=swap" rel="stylesheet">
<style>
:root{
  --pink:#e6157f;
  --pink-soft:#f06aa8;
  --ink:#222;
  --muted:#666;
  --cream:#f2f0ea;
  --footer:#1f1f1f;
  --hero-dark:#2a0f22;
  --white:#fff;
}
*{box-sizing:border-box;margin:0;padding:0}
html,body{width:1200px;height:2479px;overflow:hidden}
body{position:relative;font-family:'Lato',sans-serif;color:var(--ink);background:var(--white)}
.abs{position:absolute}

/* hero */
.hero{left:0;top:0;width:1200px;height:760px;background:radial-gradient(ellipse at 30% 20%,#7a2055 0%,#4a1637 45%,#2a0f22 100%)}
.nav{left:0;top:46px;width:1200px;height:20px}
.nav a{position:absolute;transform:translateX(-50%);color:var(--white);font-size:12px;font-weight:700;text-decoration:none;letter-spacing:.3px;white-space:nowrap}
.nav a.active{color:var(--pink-soft)}
.brand{position:absolute;left:600px;top:-8px;transform:translateX(-50%);color:var(--white);font-size:26px;font-weight:700;white-space:nowrap;display:flex;align-items:center;gap:8px}
.brand .dot{width:12px;height:12px;border-radius:50%;background:var(--pink)}
.stage{left:51px;top:109px;width:1098px;height:593px;background:#0d0a0d}
.stage-photo{left:10px;top:0;width:1088px;height:499px;background:linear-gradient(120deg,#2a0d10 0%,#8a2a1a 35%,#c2561f 55%,#4a1b12 80%,#160909 100%)}
.hero-title{left:102px;top:240px;font-family:'Open Sans',sans-serif;font-weight:800;font-size:90px;line-height:.92;color:#c8a8c8;letter-spacing:-1px}
.hero-text{left:107px;top:420px;width:350px;font-size:13px;line-height:21px;color:var(--white)}
.play-big{left:565px;top:330px;width:80px;height:80px}
.player{left:51px;top:608px;width:1098px;height:94px;background:#171317}
.player .title{position:absolute;left:160px;top:26px;color:#cfc8cf;font-size:17px}
.player .time{position:absolute;right:50px;top:27px;color:#9a929a;font-size:12px}
.player .bar{position:absolute;left:160px;top:57px;width:888px;height:3px;background:#3a343a}
.ctrl{left:100px;top:638px;width:94px;height:52px}

/* about */
.ghost{color:#f0f1f4;font-family:'Open Sans',sans-serif;font-weight:800;font-size:150px;line-height:1;letter-spacing:-3px}
.about-ghost{left:-8px;top:720px}
.section-title{font-size:33px;font-weight:700;color:var(--pink);white-space:nowrap;transform:translateX(-50%)}
.about-title{left:617px;top:815px}
.about-lead{left:99px;top:878px;width:540px;font-size:19px;font-weight:700;line-height:32px;color:#1d1d1d}
.about-body{left:97px;top:985px;width:530px;font-size:13.5px;line-height:25px;color:#555}
.about-art{left:670px;top:810px;width:460px;height:281px;background:radial-gradient(ellipse at 50% 45%,#e8e8e8 0%,#f6f6f6 55%,#fff 100%)}

/* artists */
.artists{left:0;top:1132px;width:1200px;height:496px;background:var(--cream)}
.artists-title{left:600px;top:1168px}
.artist-frame{left:150px;top:1240px;width:258px;height:286px;background:#ddd9d0}
.artist-photo{left:160px;top:1230px;width:258px;height:286px;background:linear-gradient(150deg,#2b4a78 0%,#51392e 55%,#1c1c22 100%)}
.artist-controls{left:150px;top:1540px;width:270px;height:38px}
.tracks{left:456px;top:1232px;width:607px}
.track{position:relative;height:69px;border-bottom:1px solid #ec9cc2;display:flex;align-items:center;font-size:14px;color:#333}
.track .num{width:47px}
.track .name{width:213px}
.track .dur{width:127px}
.track.active{color:var(--pink)}
.btn{display:inline-block;border:1px solid var(--pink);color:var(--pink);font-size:13px;text-align:center;line-height:28px;height:30px;background:transparent}
.track .btn{position:absolute;top:19px;width:104px}
.track .paused{left:387px}
.track .dl{left:501px}
.track.active .btn{background:var(--pink);color:var(--white)}
.artist-name{left:456px;top:1457px;font-size:15px;font-weight:700;color:#222}
.artist-bio{left:456px;top:1484px;width:470px;font-size:13px;line-height:24px;color:#555}
.view-rate{left:456px;top:1542px;width:98px;height:33px;line-height:31px}

/* songs */
.songs-ghost{left:-8px;top:1580px}
.songs-title{left:600px;top:1672px}
.song{top:1752px;width:283px}
.song .art{width:283px;height:278px;box-shadow:0 10px 14px -8px rgba(0,0,0,.35)}
.song h3{margin-top:14px;text-align:center;color:var(--pink);font-size:19px;font-weight:700}
.song p{text-align:center;font-size:12px;color:#555;margin-top:2px}

/* footer */
.footer{left:0;top:2126px;width:1200px;height:291px;background:var(--footer)}
.footer .brand{top:72px;font-size:28px}
.footer-text{left:0;top:142px;width:1200px;text-align:center;font-style:italic;font-size:13px;line-height:22px;color:#e8e8e8}
.social{top:218px;width:24px;height:24px;border-radius:50%;border:2px solid var(--white)}
.copyright{left:0;top:2441px;width:1200px;text-align:center;font-size:13px;color:var(--pink)}
</style>
</head>
<body>

<section class="abs hero">
  <nav class="abs nav">
    <a class="active" style="left:160px">HOME</a>
    <a style="left:270px">ABOUT</a>
    <a style="left:418px">DOWNLOAD MUSIC</a>
    <span class="brand">Velora Music<span class="dot"></span></span>
    <a style="left:747px">PHOTOS</a>
    <a style="left:886px">LIST OF MUSIC</a>
    <a style="left:1027px">CONTACT</a>
  </nav>
  <div class="abs stage">
    <div class="abs stage-photo" role="img" aria-label="Concert photo of a singer and a guitarist performing under warm stage lights"></div>
  </div>
  <h1 class="abs hero-title">Velora<br>Music</h1>
  <p class="abs hero-text">Consectetur adipiscing elit, sed do eiusmod tempor incid idunt ut labore et dolore magna aliqua.Ut enim ad minim veniam, quis nostrud exercitation ullamco laboris nisi ut aliquip ex ea commodo consequat.</p>
  <svg class="abs play-big" viewBox="0 0 80 80" aria-label="Play video">
    <circle cx="40" cy="40" r="36" fill="none" stroke="#fff" stroke-width="5"/>
    <path d="M32 24 L56 40 L32 56 Z" fill="#fff"/>
  </svg>
  <div class="abs player">
    <span class="title">Velora Music</span>
    <span class="time">00.00</span>
    <span class="bar"></span>
  </div>
  <svg class="abs ctrl" viewBox="0 0 94 52" aria-label="Player controls">
    <rect x="0" y="12" width="94" height="28" rx="14" fill="#e8e4e8"/>
    <path d="M12 26 L17 22 V30 Z M17 26 L22 22 V30 Z" fill="#333"/>
    <path d="M82 26 L77 22 V30 Z M77 26 L72 22 V30 Z" fill="#333"/>
    <circle cx="47" cy="26" r="24" fill="#d9322a"/>
    <path d="M42 18 L55 26 L42 34 Z" fill="#fff"/>
  </svg>
</section>

<div class="abs ghost about-ghost">About</div>
<h2 class="abs section-title about-title">About</h2>
<p class="abs about-lead">Consectetur adipiscing elit, sed do eiusmod tempor incididunt ut labore et dolore magna aliqua. Ut enim ad minim veniam, quisnotr ud exercitation ullamco laboris nisi ut aliquip</p>
<p class="abs about-body">Perspiciatis unde omnis iste natus error sit voluptatem accusantium doloremque lau dantium, totam rem aperiam, eaque ipsa quae ab illo inventore veritatis et quasi archi tecto beata vitae dicta sunt explicabo. Nemo enim ipsam voluptatem quia voluptas sit aspernatur aut odit aut fugit, sed quia consequuntur</p>
<div class="abs about-art" role="img" aria-label="Illustration of a woman in headphones at a keyboard with red music notes flowing outward"></div>

<section class="abs artists"></section>
<h2 class="abs section-title artists-title">Top artists</h2>
<div class="abs artist-frame"></div>
<div class="abs artist-photo" role="img" aria-label="Photo of a smiling artist wearing headphones at a studio microphone"></div>
<svg class="abs artist-controls" viewBox="0 0 270 38" aria-label="Artist player controls">
  <path d="M9 15 H13 L18 11 V27 L13 23 H9 Z" fill="#333"/>
  <path d="M20 15 Q23 19 20 23" stroke="#333" stroke-width="1.5" fill="none"/>
  <path d="M88 19 L94 14 V24 Z M94 19 L100 14 V24 Z" fill="#e6157f"/>
  <circle cx="140" cy="19" r="17" fill="none" stroke="#e6157f" stroke-width="2"/>
  <path d="M135 12 L147 19 L135 26 Z" fill="none" stroke="#e6157f" stroke-width="2"/>
  <path d="M192 19 L186 14 V24 Z M186 19 L180 14 V24 Z" fill="#e6157f"/>
  <circle cx="257" cy="19" r="5" fill="none" stroke="#333" stroke-width="3"/>
</svg>
<div class="abs tracks">
  <div class="track active"><span class="num">01</span><span class="name">Architecto beatae vitae</span><span class="dur">04.12</span><span class="btn paused">Paused</span><span class="btn dl">Download</span></div>
  <div class="track"><span class="num">02</span><span class="name">Voluptatem quia voluptas</span><span class="dur">03.17</span><span class="btn paused">Paused</span><span class="btn dl">Download</span></div>
  <div class="track"><span class="num">03</span><span class="name">Consequuntur magni</span><span class="dur">02.12</span><span class="btn paused">Paused</span><span class="btn dl">Download</span></div>
</div>
<h3 class="abs artist-name">ARCHITECTO BEATAE VITAE</h3>
<p class="abs artist-bio">Perspiciatis unde omnis iste natus error sit voluptatem accusantium dolore mque dantium, totam rem aperiam, eaque ipsa quae ab illo</p>
<span class="abs btn view-rate">View Rate</span>

<div class="abs ghost songs-ghost">Songs</div>
<h2 class="abs section-title songs-title">Top songs</h2>
<article class="abs song" style="left:98px">
  <div class="art" role="img" aria-label="Photo of a DJ at turntables in purple and blue club light" style="background:linear-gradient(135deg,#c9b8f0 0%,#7a3fc6 40%,#3a1a6a 100%)"></div>
  <h3>RnB</h3><p>architecto beatae vitae</p>
</article>
<article class="abs song" style="left:458px">
  <div class="art" role="img" aria-label="Photo of two musicians performing on a red lit stage" style="background:linear-gradient(160deg,#b3262a 0%,#3a1a1a 55%,#151515 100%)"></div>
  <h3>Hip hop</h3><p>architecto beatae vitae</p>
</article>
<article class="abs song" style="left:818px">
  <div class="art" role="img" aria-label="Photo of a singer playing a banjo under blue stage light" style="background:linear-gradient(150deg,#4a3aa8 0%,#2a2060 50%,#6a4a3a 100%)"></div>
  <h3>Rock</h3><p>architecto beatae vitae</p>
</article>

<footer class="abs footer">
  <span class="brand">Velora Music<span class="dot"></span></span>
  <p class="abs footer-text">Perspiciatis unde omnis iste natus error sit voluptatem accusantium doloremque laudantium,<br>totam rem aperiam, eaque ipsa quae ab illo inventore veritatis et quasi</p>
  <span class="abs social" style="left:528px" aria-label="Social link"></span>
  <span class="abs social" style="left:585px" aria-label="Social link"></span>
  <span class="abs social" style="left:643px" aria-label="Social link"></span>
</footer>
<p class="abs copyright">Copyright © 2016 Allrights reserved</p>

</body>
</html>
```